New Business Card Design for Manufacturing

We are an engineering/manufacturing company that offers Advanced machining/assembly/engineering services, as well as innovative products for the heavy duty engine cooling markets.

We are looking to get a new business card designed that is clean and modern looking, but still fits the wide range of technical/skilled work we do.

- We hope to use this design as the base for other design work in new Presentations, web, and print work.

Industry/Entity Type

Engineering

Contact Information for Business Card

Our preferred color of blue is (RGB) 22/71/159 but can vary slightly from that color. Our content will be our Logo and full company name (Vantrell Forge Works, Inc.), company address, name, job title, phone number with extension, cell number, fax number, website, and email address on the cards.
We'd like the full company name next to the logo, but we are open to other interpretations of that layout.
Preferably, we would like the back side to be clean with just our logo, and the front to contain all of the contact information.

Colors
2f74b4
0355a3
85abd2

Requirements
Must have
• - Logo, company name, needed content - We are open to interpretation beyond that.
• - Standard size business card.
• - Horizontal orientation.
• - Enough space for lengthy names / job titles (for example, a job title could read "Directory of Human Resources" or "V.P. of Governmental Affairs"). We need this to look clean, whether the title be short (CEO) or long (as described above).

```html
<!DOCTYPE html>
<html lang="en">
<head>
<meta charset="utf-8">
<title>Vantrell Forge Works – Business Card</title>
<link href="https://fonts.googleapis.com/css2?family=Roboto:wght@400;500;700&family=Roboto+Condensed:wght@500&display=swap" rel="stylesheet">
<style>
  :root {
    --brand-blue: #0f52a2;
    --card-white: #fbfbfb;
    --text-dark: #1e1e1e;
    --text-grey: #555a60;
    --page-bg: #e8e6e2;
  }
  * { margin: 0; padding: 0; box-sizing: border-box; }
  html, body { width: 1200px; height: 960px; overflow: hidden; }
  body {
    background: var(--page-bg);
    font-family: "Roboto", Arial, sans-serif;
    position: relative;
  }
  .card {
    position: absolute;
    width: 600px;
    height: 342px;
    border-radius: 18px;
  }
  .card--front {
    left: 302px; top: 129px;
    background: var(--card-white);
  }
  .card--back {
    left: 299px; top: 489px;
    background: var(--brand-blue);
  }
  .company-name {
    position: absolute;
    font-family: "Roboto", Arial, sans-serif;
    font-weight: 700;
    text-transform: uppercase;
    line-height: 1.02;
  }
  .card--front .company-name {
    right: 52px; top: 48px;
    color: var(--brand-blue);
    font-size: 27px;
    text-align: right;
  }
  .card--back .company-name {
    left: 0; right: 0; top: 110px;
    color: #fff;
    font-size: 46px;
    text-align: center;
  }
  .person-name {
    position: absolute;
    left: 37px; top: 198px;
    font-family: "Roboto Condensed", "Arial Narrow", sans-serif;
    font-weight: 500;
    font-size: 27px;
    color: var(--brand-blue);
    letter-spacing: 0.2px;
  }
  .job-title {
    position: absolute;
    left: 37px; top: 229px;
    font-size: 14.5px;
    color: var(--text-dark);
  }
  .divider {
    position: absolute;
    left: 37px; top: 254px;
    width: 513px; height: 2px;
    background: var(--brand-blue);
  }
  .contact-row {
    position: absolute;
    left: 37px;
    display: flex;
    align-items: center;
    gap: 3px;
    font-size: 14px;
    color: var(--text-grey);
    white-space: nowrap;
  }
  .contact-row--address { top: 268px; }
  .contact-row--lines { top: 290px; }
  .contact-item { display: flex; align-items: center; gap: 3px; margin-right: 3px; }
  .icon { width: 17px; height: 17px; flex: none; }
  .website {
    position: absolute;
    left: 0; right: 0; top: 283px;
    text-align: center;
    color: #fff;
    font-size: 14px;
    font-weight: 500;
    letter-spacing: 2.4px;
  }
</style>
</head>
<body>

  <section class="card card--front">
    <div class="company-name">Vantrell Forge<br>Works, Inc.</div>

    <div class="person-name">DANA WHITLOCK</div>
    <div class="job-title">V.P. of Governmental Affairs</div>
    <div class="divider"></div>

    <div class="contact-row contact-row--address">
      <svg class="icon" viewBox="0 0 16 16"><circle cx="8" cy="8" r="8" fill="#0f52a2"/><path d="M8 3.5a3 3 0 0 0-3 3c0 2.2 3 5.8 3 5.8s3-3.6 3-5.8a3 3 0 0 0-3-3z" fill="#fff"/><circle cx="8" cy="6.5" r="1.1" fill="#0f52a2"/></svg>
      <span>412 Alder Ridge Road, Fairbanks, Alaska 99701</span>
    </div>

    <div class="contact-row contact-row--lines">
      <span class="contact-item">
        <svg class="icon" viewBox="0 0 16 16"><circle cx="8" cy="8" r="8" fill="#0f52a2"/><path d="M5.2 4c.4-.3.9-.2 1.1.2l.7 1.3c.2.4.1.8-.2 1l-.5.4c.4.9 1.1 1.7 2 2.2l.4-.5c.3-.3.7-.4 1-.2l1.3.7c.4.2.5.7.2 1.1l-.6.7c-.5.5-1.3.6-2 .2-1.8-1-3.3-2.5-4.2-4.3-.3-.7-.2-1.4.3-1.9z" fill="#fff"/></svg>
        <span>555 214 0187</span>
      </span>
      <span class="contact-item">
        <svg class="icon" viewBox="0 0 16 16"><circle cx="8" cy="8" r="8" fill="#0f52a2"/><rect x="5.5" y="3.5" width="5" height="9" rx="1" fill="#fff"/><rect x="6.4" y="4.6" width="3.2" height="6" fill="#0f52a2"/></svg>
        <span>555 390 2261</span>
      </span>
      <span class="contact-item">
        <svg class="icon" viewBox="0 0 16 16"><circle cx="8" cy="8" r="8" fill="#0f52a2"/><rect x="4" y="5" width="8" height="6" rx="0.8" fill="#fff"/><path d="M4.3 5.4 8 8.3l3.7-2.9" stroke="#0f52a2" stroke-width="0.9" fill="none"/></svg>
        <span>dana@vforge.com</span>
      </span>
      <span class="contact-item">
        <svg class="icon" viewBox="0 0 16 16"><circle cx="8" cy="8" r="8" fill="#0f52a2"/><circle cx="8" cy="8" r="4" fill="#fff"/><path d="M6 5.5c1 .6 1.2 1.6.4 2.3-.6.5-.4 1.4.3 1.8M9.8 6.2c-.6.8.2 1.4.9 1.2" stroke="#0f52a2" stroke-width="1" fill="none"/></svg>
        <span>www.vforge.com</span>
      </span>
    </div>
  </section>

  <section class="card card--back">
    <div class="company-name">Vantrell Forge<br>Works, Inc.</div>
    <div class="website">www.vantrellforgeworks.com</div>
  </section>

</body>
</html>
```